Business Card Design Project

Business Card
We are rebranding with a new logo
Industry/Entity Type
Business
Contact Information for Business Card
Dennis Morvale +61 487215963 dennis@quorv.com.au P.O. Box 872 Fernlow QLD 4309
Requirements
Must have
- Logo

```html
<!DOCTYPE html>
<html lang="en">
<head>
<meta charset="UTF-8">
<title>Quorv International – Business Card</title>
<link href="https://fonts.googleapis.com/css2?family=Open+Sans:wght@400;700&display=swap" rel="stylesheet">
<style>
  :root {
    --page-bg: #e4e4e4;
    --card-white: #ffffff;
    --card-black: #050505;
    --band-name: #858585;
    --band-info: #575757;
    --accent-blue: #4fb3e8;
    --icon-blue: #5bbcea;
    --text-light: #ffffff;
    --brand-ink: #1c2a3a;
  }
  * { margin: 0; padding: 0; box-sizing: border-box; }
  html, body {
    width: 1200px;
    height: 1000px;
    overflow: hidden;
    background: var(--page-bg);
    font-family: "Open Sans", Arial, sans-serif;
  }
  .business-card {
    position: absolute;
    left: 110px;
    top: 220px;
    width: 980px;
    height: 560px;
    display: flex;
    box-shadow: 0 12px 30px rgba(0,0,0,0.28);
  }
  .card-front {
    width: 500px;
    height: 100%;
    background: var(--card-white);
    display: flex;
    align-items: center;
    justify-content: center;
  }
  .brand-name {
    color: var(--brand-ink);
    font-weight: 700;
    font-size: 30px;
    line-height: 1.25;
    letter-spacing: 3px;
    text-align: center;
    text-transform: uppercase;
    margin-top: -20px;
  }
  .brand-name .brand-word {
    display: block;
    font-size: 30px;
    letter-spacing: 8px;
  }
  .card-details {
    position: relative;
    width: 480px;
    height: 100%;
    background: var(--card-black);
  }
  .accent-rule {
    position: absolute;
    left: 0;
    top: 35px;
    width: 4px;
    height: 490px;
    background: var(--accent-blue);
    border-radius: 0 4px 4px 0;
  }
  .band {
    position: absolute;
    left: 0;
    width: 100%;
    border-bottom: 2px solid var(--accent-blue);
    display: flex;
    align-items: center;
    color: var(--text-light);
  }
  .band-name {
    top: 60px;
    height: 85px;
    background: var(--band-name);
    padding-left: 134px;
  }
  .holder-name {
    font-weight: 700;
    font-size: 35px;
    letter-spacing: 1px;
  }
  .band-info {
    height: 68px;
    background: var(--band-info);
    padding-left: 109px;
  }
  .band-phone { top: 196px; }
  .band-email { top: 311px; }
  .band-address { top: 427px; }
  .contact-icon {
    width: 44px;
    height: 44px;
    flex: none;
    margin-right: 22px;
  }
  .contact-text {
    font-size: 20px;
    letter-spacing: 2px;
    line-height: 1.5;
    word-spacing: 6px;
  }
</style>
</head>
<body>
  <div class="business-card">
    <section class="card-front">
      <p class="brand-name"><span class="brand-word">Quorv</span>International</p>
    </section>

    <section class="card-details">
      <div class="accent-rule"></div>

      <div class="band band-name">
        <span class="holder-name">Dennis Morvale</span>
      </div>

      <div class="band band-info band-phone">
        <svg class="contact-icon" viewBox="0 0 44 44" aria-hidden="true">
          <circle cx="22" cy="22" r="21" fill="var(--icon-blue)"/>
          <path d="M15 12c1-1 2.5-1 3.2.2l2 3.4c.6 1 .3 2-.5 2.7l-1.2 1c1 2.4 2.9 4.4 5.3 5.5l1-1.2c.7-.8 1.8-1 2.7-.5l3.4 2c1.1.7 1.2 2.2.2 3.2l-1.6 1.6c-1.4 1.4-3.6 1.6-5.3.6-4.6-2.6-8.3-6.3-10.8-10.9-.9-1.7-.7-3.9.7-5.2z" fill="#fff"/>
        </svg>
        <span class="contact-text">+61 487215963</span>
      </div>

      <div class="band band-info band-email">
        <svg class="contact-icon" viewBox="0 0 44 44" aria-hidden="true">
          <circle cx="22" cy="22" r="21" fill="var(--icon-blue)"/>
          <rect x="11" y="14" width="22" height="16" rx="1.5" fill="#fff"/>
          <path d="M11.5 15 22 23.5 32.5 15" fill="none" stroke="var(--icon-blue)" stroke-width="1.6"/>
        </svg>
        <span class="contact-text">dennis@quorv.com.au</span>
      </div>

      <div class="band band-info band-address">
        <svg class="contact-icon" viewBox="0 0 44 44" aria-hidden="true">
          <circle cx="22" cy="22" r="21" fill="var(--icon-blue)"/>
          <g fill="none" stroke="#fff" stroke-width="1.8">
            <circle cx="22" cy="22" r="11"/>
            <ellipse cx="22" cy="22" rx="5" ry="11"/>
            <line x1="11" y1="22" x2="33" y2="22"/>
            <path d="M13 16.5h18M13 27.5h18"/>
          </g>
        </svg>
        <span class="contact-text">P.O. Box 872<br>Fernlow QLD 4309</span>
      </div>
    </section>
  </div>
</body>
</html>
```